Online interactive calendar for training organisation

We have a new website being made and need a design for an online calendar that is interactive and very simple and easy to use. On our main page this calendar will include all of our courses (approx 30 different ones with up to 8 different locations). On our sub pages which have course information, the calendar will only include details of that specific course. Details needed are: Course code, course name/title, date, duration (1/2 day - 5 days), location, price, discount price. Maybe also a key for available or limited spots left? We want a section at the top of the calendar to be able to filter by location or course, and maybe to filter by month also? I have included a spreadsheet with a sample of our courses with this information. Also a sample draft of the main page on our new webpage to show the colour green which is our company colour. Main notes - we want as simple, effective and easy to use as possible.
We will need to know what plug in we can use to get the design you have created.

Target Market(s)

Mining and construction - both companies and individuals

Number of Pages Required

1 page

Colors
cadf82

Requirements
Must have
• Be simple, easy to use, effective.

```html
<!DOCTYPE html>
<html lang="en">
<head>
<meta charset="utf-8">
<title>Ridgeline Safety – Time Table</title>
<link rel="stylesheet" href="https://fonts.googleapis.com/css2?family=Roboto:wght@300;400;500;700;900&family=Roboto+Condensed:wght@300;400&display=swap">
<style>
:root{
  --stage:#8f8f8f;
  --white:#ffffff;
  --green:#8cc63f;
  --price:#7dbb2e;
  --ink:#1d1d1d;
  --muted:#555555;
  --line:#bdbdbd;
  --soft:#f1f1f1;
  --tag:#ececec;
  --dark:#252525;
  --brand:#d6262c;
}
*{box-sizing:border-box;margin:0;padding:0}
html,body{width:1200px;height:2655px;overflow:hidden}
body{background:var(--stage);font-family:"Roboto",sans-serif;color:var(--ink);position:relative}
.board{position:absolute;background:var(--white);box-shadow:0 2px 10px rgba(0,0,0,.25)}
.board--timetable{left:50px;top:58px;width:1095px;height:673px}
.board--page{left:52px;top:772px;width:1090px;height:1828px;overflow:hidden}

/* timetable block */
.timetable{position:absolute;width:800px;height:620px}
.timetable__title{position:absolute;left:0;right:0;top:37px;text-align:center;font-weight:700;font-size:23px;letter-spacing:.5px}
.timetable__rule{position:absolute;left:382px;top:76px;width:46px;height:3px;background:#b0b0b0}
.filter{position:absolute;top:120px;width:190px;height:40px;border:2px solid #cfcfcf;padding:6px 10px;font-size:10px;line-height:12px}
.filter--active{border-color:var(--green)}
.filter__label{font-weight:700;letter-spacing:.3px}
.filter__label b{color:var(--brand)}
.filter__value{color:#444}
.filter--active .filter__value{color:var(--green);font-weight:500}
.filter svg{position:absolute;right:12px;top:14px}
.card{position:absolute;width:259px;height:199px;border:1px solid #c7c7c7;background:var(--white)}
.card__date{position:absolute;left:25px;top:18px;font-size:11.5px;color:#333;padding-bottom:5px;border-bottom:2px solid #d0d0d0}
.card__title{position:absolute;left:25px;top:53px;width:170px;font-size:15px;line-height:18px;color:#111;font-weight:400}
.card__title b{color:var(--brand);font-weight:400}
.card__tags{position:absolute;left:22px;top:108px;height:23px;display:flex}
.tag-duration{border:1px solid #c9c9c9;background:var(--tag);font-size:11.5px;padding:0 8px;line-height:21px;margin-right:-2px}
.tag-location{background:var(--ink);color:var(--white);font-weight:700;font-size:13px;line-height:23px;padding:0 18px 0 14px;clip-path:polygon(8px 0,100% 0,calc(100% - 8px) 100%,0 100%)}
.card__price{position:absolute;left:25px;top:144px;font-size:22px;font-weight:700;color:var(--price)}
.discount{position:absolute;right:-1px;bottom:-1px;width:84px;height:53px;background:linear-gradient(135deg,#dcdcdc 0 14px,#f2f2f2 14px);border:1px solid #cfcfcf;padding:14px 0 0 13px;clip-path:polygon(6px 0,100% 0,100% 100%,0 100%,0 8px)}
.discount__label{font-size:9.5px;color:#444;letter-spacing:.3px}
.discount__value{font-size:15px;color:#111;margin-top:2px}

/* page header */
.topbar{position:absolute;left:0;top:0;width:100%;height:28px;background:var(--green)}
.social{position:absolute;left:206px;top:7px;display:flex;gap:5px}
.social span{width:16px;height:16px;border-radius:50%;background:#111;display:block}
.student-access{position:absolute;left:708px;top:4px;width:77px;height:19px;background:#1f1f1f;color:var(--white);font-size:8px;font-weight:700;text-align:center;line-height:19px;border-radius:2px}
.search{position:absolute;left:790px;top:4px;width:97px;height:19px;background:var(--white);border-radius:2px}
.search svg{position:absolute;right:7px;top:5px}
.header{position:absolute;left:0;top:28px;width:100%;height:64px;background:var(--white)}
.brand{position:absolute;left:206px;top:12px;display:flex;align-items:center;gap:8px}
.brand__mark{width:34px;height:34px;border-radius:50%;background:var(--brand)}
.brand__name{font-weight:900;font-size:19px;color:var(--brand);letter-spacing:.5px;line-height:20px}
.brand__tag{font-size:8px;font-weight:500;color:#333;letter-spacing:.5px;margin-top:3px}
.nav{position:absolute;left:561px;top:26px;display:flex;gap:16px;font-size:8.5px;color:#333}
.nav .is-current{color:var(--green)}

/* difference */
.difference{position:absolute;left:0;top:92px;width:100%;height:487px;background:var(--soft)}
.difference__title{position:absolute;left:0;right:0;top:36px;text-align:center;font-family:"Roboto Condensed",sans-serif;font-weight:400;font-size:29px;line-height:34px;color:#1a1a1a}
.difference__sub{position:absolute;left:0;right:0;top:75px;text-align:center;font-size:10px;color:#333}
.difference__rule{position:absolute;left:525px;top:102px;width:45px;height:2px;background:var(--green)}
.tile{position:absolute;width:125px}
.tile__photo{height:123px;border-radius:2px}
.tile__label{text-align:center;font-size:10.5px;color:#333;margin-top:12px}

/* hero */
.hero{position:absolute;left:0;top:1267px;width:100%;height:368px;background:linear-gradient(100deg,#6f6446 0%,#a58f3e 22%,#7d7660 45%,#c9c8c2 65%,#e6e6e3 100%)}
.hero__frame{position:absolute;left:694px;top:60px;width:218px;height:250px;border:14px solid rgba(255,255,255,.85)}
.hero__headline{position:absolute;left:590px;top:140px;font-size:33px;font-weight:700;line-height:38px;color:#222;white-space:nowrap;letter-spacing:-.2px}
.hero__banner{position:absolute;left:590px;top:226px;width:297px;height:20px;background:var(--green);color:var(--white);font-size:8.5px;line-height:20px;text-align:center}

/* footer */
.footer{position:absolute;left:0;top:1635px;width:100%;height:160px;background:var(--dark);color:#ddd}
.footer .brand{top:48px}
.footer .brand__name{color:var(--brand)}
.follow{position:absolute;left:245px;top:95px;font-size:10px;display:flex;align-items:center;gap:5px}
.follow span{width:15px;height:15px;background:#fff;display:block}
.follow span:first-child{margin-left:6px}
.footer .nav{top:64px;color:#ccc}
.contact{position:absolute;top:95px;display:flex;align-items:center;gap:9px;font-size:9px;color:#ccc}
.contact__icon{width:20px;height:20px;background:#fff;display:flex;align-items:center;justify-content:center}
.to-top{position:absolute;left:915px;top:142px;width:33px;height:32px;background:var(--white);border:1px solid #ccc;display:flex;align-items:center;justify-content:center}
.bottombar{position:absolute;left:0;top:1795px;width:100%;height:33px;background:var(--green);text-align:center;font-size:8.5px;line-height:33px;color:#222}
</style>
</head>
<body>

<section class="board board--timetable">
  <div class="timetable" style="left:180px;top:0">
    <h2 class="timetable__title">TIME TABLE</h2>
    <div class="timetable__rule"></div>
    <div class="filter filter--active" style="left:98px"><div class="filter__label">LOCATION<b>*</b></div><div class="filter__value">YATALA</div><svg width="10" height="7" viewBox="0 0 10 7"><path d="M1 1l4 4 4-4" fill="none" stroke="#222" stroke-width="1.6"/></svg></div>
    <div class="filter" style="left:304px"><div class="filter__label">COURSE<b>*</b></div><div class="filter__value">SELECT COURSE</div><svg width="10" height="7" viewBox="0 0 10 7"><path d="M1 1l4 4 4-4" fill="none" stroke="#222" stroke-width="1.6"/></svg></div>
    <div class="filter" style="left:512px"><div class="filter__label">MONTH<b>*</b></div><div class="filter__value">SELECT MONTH</div><svg width="10" height="7" viewBox="0 0 10 7"><path d="M1 1l4 4 4-4" fill="none" stroke="#222" stroke-width="1.6"/></svg></div>

    <article class="card" style="left:0;top:203px"><div class="card__date">29 October 2019 &nbsp;| &nbsp;8:00 AM</div><h3 class="card__title">RIIHAN304D Work safely at heights <b>*</b></h3><div class="card__tags"><span class="tag-duration">1 DAY</span><span class="tag-location">YATALA</span></div><div class="card__price">$500.00</div><div class="discount"><div class="discount__label">DISCOUNT</div><div class="discount__value">$120.00</div></div></article>
    <article class="card" style="left:271px;top:203px"><div class="card__date">29 October 2019 &nbsp;| &nbsp;8:00 AM</div><h3 class="card__title">RIIHAN304D Work safely at heights</h3><div class="card__tags"><span class="tag-duration">1 DAY</span><span class="tag-location">YATALA</span></div><div class="card__price">$500.00</div><div class="discount"><div class="discount__label">DISCOUNT</div><div class="discount__value">$120.00</div></div></article>
    <article class="card" style="left:541px;top:203px"><div class="card__date">30 January 2020 &nbsp;| &nbsp;8:00 AM</div><h3 class="card__title">HLTAID005 Confined space - practical</h3><div class="card__tags"><span class="tag-duration">1/2 DAY</span><span class="tag-location">YATALA</span></div><div class="card__price">$80.00</div></article>
    <article class="card" style="left:0;top:417px"><div class="card__date">15 November 2020 &nbsp;| &nbsp;8:00 AM</div><h3 class="card__title">HLTAID001 First Aid - practical only</h3><div class="card__tags"><span class="tag-duration">1/2 DAY</span><span class="tag-location">YATALA</span></div><div class="card__price">$80.00</div></article>
    <article class="card" style="left:271px;top:417px"><div class="card__date">28 October 2019 &nbsp;| &nbsp;8:00 AM</div><h3 class="card__title">CPCCCM208 Dogging &amp; TLILIC0005</h3><div class="card__tags"><span class="tag-duration">1 DAY</span><span class="tag-location">YATALA</span></div><div class="card__price">$500.00</div><div class="discount"><div class="discount__label">DISCOUNT</div><div class="discount__value">$1200.00</div></div></article>
  </div>
</section>

<section class="board board--page">
  <div class="topbar">
    <div class="social"><span></span><span></span><span></span><span></span></div>
    <div class="student-access">Student Access</div>
    <div class="search"><svg width="9" height="9" viewBox="0 0 10 10"><circle cx="4" cy="4" r="3" fill="none" stroke="#222" stroke-width="1.6"/><path d="M6.3 6.3L9 9" stroke="#222" stroke-width="1.6"/></svg></div>
  </div>
  <header class="header">
    <div class="brand"><span class="brand__mark"></span><div><div class="brand__name">RIDGELINE SAFETY</div><div class="brand__tag">SAFETY AND TRAINING</div></div></div>
    <nav class="nav"><span class="is-current">Home</span><span>Courses</span><span>Our Services</span><span>About us</span><span>Funding</span><span>Locations</span><span>Contact us</span></nav>
  </header>

  <section class="difference">
    <h2 class="difference__title">THE RIDGELINE SAFETY DIFFERENCE</h2>
    <p class="difference__sub">Committed to helping our students succeed.</p>
    <div class="difference__rule"></div>
    <div class="tile" style="left:205px;top:131px"><div class="tile__photo" role="img" aria-label="Loader working in a quarry" style="background:linear-gradient(160deg,#7a776f,#a99a5a,#5c5a55)"></div><div class="tile__label">All Courses</div></div>
    <div class="tile" style="left:342px;top:131px"><div class="tile__photo" role="img" aria-label="Gloved handshake" style="background:linear-gradient(160deg,#4f8ed0,#c9d7e6,#e0c04a)"></div><div class="tile__label">Funded courses</div></div>
    <div class="tile" style="left:481px;top:131px"><div class="tile__photo" role="img" aria-label="Red tipper truck at a mine" style="background:linear-gradient(160deg,#8a8a86,#c24a3e,#6d6c68)"></div><div class="tile__label">Mining</div></div>
    <div class="tile" style="left:622px;top:131px"><div class="tile__photo" role="img" aria-label="Excavator on a work site" style="background:linear-gradient(160deg,#6c6a66,#c59c33,#4c4a46)"></div><div class="tile__label">Standard 11</div></div>
    <div class="tile" style="left:762px;top:131px"><div class="tile__photo" role="img" aria-label="Workers in harnesses on a platform" style="background:linear-gradient(160deg,#9eb0a0,#5c6b5a,#2e3a30)"></div><div class="tile__label">Work safely at heights</div></div>
    <div class="tile" style="left:205px;top:297px"><div class="tile__photo" role="img" aria-label="Business meeting at a desk" style="background:linear-gradient(160deg,#9a9ca0,#3d3f44,#c8c6c0)"></div><div class="tile__label">Corporate clients</div></div>
    <div class="tile" style="left:342px;top:297px"><div class="tile__photo" role="img" aria-label="Students around a laptop" style="background:linear-gradient(160deg,#d9d3c9,#e0a23a,#5f7fa8)"></div><div class="tile__label">Online courses</div></div>
    <div class="tile" style="left:481px;top:297px"><div class="tile__photo" role="img" aria-label="Engineers in hard hats reviewing plans" style="background:linear-gradient(160deg,#7aa8d8,#d9d34a,#d8dce0)"></div><div class="tile__label">RPL's &amp; VOC's</div></div>
    <div class="tile" style="left:622px;top:297px"><div class="tile__photo" role="img" aria-label="Operator with elevated work platform" style="background:linear-gradient(160deg,#8fa36e,#e3c52e,#7b8068)"></div><div class="tile__label">Plant &amp; Equipment</div></div>
    <div class="tile" style="left:762px;top:297px"><div class="tile__photo" role="img" aria-label="Construction worker on site" style="background:linear-gradient(160deg,#6b88b8,#c09b63,#3d4150)"></div><div class="tile__label">Construction</div></div>
  </section>

  <div class="timetable" style="left:150px;top:599px">
    <h2 class="timetable__title">TIME TABLE</h2>
    <div class="timetable__rule"></div>
    <div class="filter filter--active" style="left:98px"><div class="filter__label">LOCATION<b>*</b></div><div class="filter__value">YATALA</div><svg width="10" height="7" viewBox="0 0 10 7"><path d="M1 1l4 4 4-4" fill="none" stroke="#222" stroke-width="1.6"/></svg></div>
    <div class="filter" style="left:304px"><div class="filter__label">COURSE<b>*</b></div><div class="filter__value">SELECT COURSE</div><svg width="10" height="7" viewBox="0 0 10 7"><path d="M1 1l4 4 4-4" fill="none" stroke="#222" stroke-width="1.6"/></svg></div>
    <div class="filter" style="left:512px"><div class="filter__label">MONTH<b>*</b></div><div class="filter__value">SELECT MONTH</div><svg width="10" height="7" viewBox="0 0 10 7"><path d="M1 1l4 4 4-4" fill="none" stroke="#222" stroke-width="1.6"/></svg></div>

    <article class="card" style="left:0;top:203px"><div class="card__date">29 October 2019 &nbsp;| &nbsp;8:00 AM</div><h3 class="card__title">RIIHAN304D Work safely at heights <b>*</b></h3><div class="card__tags"><span class="tag-duration">1 DAY</span><span class="tag-location">YATALA</span></div><div class="card__price">$500.00</div><div class="discount"><div class="discount__label">DISCOUNT</div><div class="discount__value">$120.00</div></div></article>
    <article class="card" style="left:271px;top:203px"><div class="card__date">29 October 2019 &nbsp;| &nbsp;8:00 AM</div><h3 class="card__title">RIIHAN304D Work safely at heights</h3><div class="card__tags"><span class="tag-duration">1 DAY</span><span class="tag-location">YATALA</span></div><div class="card__price">$500.00</div><div class="discount"><div class="discount__label">DISCOUNT</div><div class="discount__value">$120.00</div></div></article>
    <article class="card" style="left:541px;top:203px"><div class="card__date">30 January 2020 &nbsp;| &nbsp;8:00 AM</div><h3 class="card__title">HLTAID005 Confined space - practical</h3><div class="card__tags"><span class="tag-duration">1/2 DAY</span><span class="tag-location">YATALA</span></div><div class="card__price">$80.00</div></article>
    <article class="card" style="left:0;top:417px"><div class="card__date">15 November 2020 &nbsp;| &nbsp;8:00 AM</div><h3 class="card__title">HLTAID001 First Aid - practical only</h3><div class="card__tags"><span class="tag-duration">1/2 DAY</span><span class="tag-location">YATALA</span></div><div class="card__price">$80.00</div></article>
    <article class="card" style="left:271px;top:417px"><div class="card__date">28 October 2019 &nbsp;| &nbsp;8:00 AM</div><h3 class="card__title">CPCCCM208 Dogging &amp; TLILIC0005</h3><div class="card__tags"><span class="tag-duration">1 DAY</span><span class="tag-location">YATALA</span></div><div class="card__price">$500.00</div><div class="discount"><div class="discount__label">DISCOUNT</div><div class="discount__value">$1200.00</div></div></article>
  </div>

  <section class="hero" role="img" aria-label="Large yellow mining haul truck on a dusty site">
    <div class="hero__frame"></div>
    <h2 class="hero__headline">Training a Safety<br>Culture that Counts</h2>
    <div class="hero__banner">NOW TRAINING - Working at Heights &amp; Confined Spaces courses</div>
  </section>

  <footer class="footer">
    <div class="brand"><span class="brand__mark"></span><div class="brand__name">RIDGELINE SAFETY</div></div>
    <div class="follow">Follow us on :-<span></span><span></span><span></span><span></span></div>
    <nav class="nav"><span>Home</span><span>Courses</span><span>Our Services</span><span>About us</span><span>Funding</span><span>Locations</span><span>Contact us</span></nav>
    <div class="contact" style="left:534px"><span class="contact__icon"><svg width="9" height="12" viewBox="0 0 10 14"><path d="M5 0a5 5 0 0 1 5 5c0 3.5-5 9-5 9S0 8.5 0 5a5 5 0 0 1 5-5z" fill="#222"/><circle cx="5" cy="5" r="1.8" fill="#fff"/></svg></span>18 Foundry Lane, Westbrook QLD 4000</div>
    <div class="contact" style="left:750px"><span class="contact__icon"><svg width="12" height="9" viewBox="0 0 12 9"><rect width="12" height="9" fill="#222"/><path d="M0 0l6 5 6-5" fill="none" stroke="#fff" stroke-width="1"/></svg></span>enquiries@ridgelinesafety.edu.au</div>
    <div class="to-top"><svg width="12" height="8" viewBox="0 0 12 8"><path d="M1 7l5-5 5 5" fill="none" stroke="#222" stroke-width="1.8"/></svg></div>
  </footer>
  <div class="bottombar">© Copyright All Right Reserved | Powered by Ridgeline Safety.</div>
</section>

</body>
</html>
```